Falkrin homes and renovations business card design.

Would like some new card designs utilizing my new logo that look professional. I am open to different colors on the logo or utilize the same ones we have. I like the original concept but would like to see some fresh ideas and build on what we have already done.

Target Market(s)

Custom home building industry, Real estate sales, Renovation projects.

Industry/Entity Type

Home Builder

Contact Information for Business Card

Falkrin Homes and Renovations
2871 96th Avenue
Frank, Alberta
T2R3W8
Home : 403- 718-4063 Cell: 403- 294-5170

My info is : Dax Falkrin, President and CEO
email: falkrinhomes@maildrop-example.net
Website: falkrinhomes-example.com
websit

Requirements
Must have
• Must Use my new logo design. I am open to different colors on the logo or utilize the same ones in the existing design. I can upload the original logo design if needed.

```html
<!DOCTYPE html>
<html lang="en">
<head>
<meta charset="utf-8">
<title>Falkrin Homes and Renovations – Business Card</title>
<link href="https://fonts.googleapis.com/css2?family=Montserrat:wght@400;500&display=swap" rel="stylesheet">
<style>
  :root {
    --backdrop: #dcdddf;
    --card-white: #ffffff;
    --card-shade: #e4e4e4;
    --ink: #222222;
    --accent-yellow: #f6b91e;
    --text-light: #ffffff;
    --text-dark: #2b2b2b;
  }
  html, body {
    margin: 0;
    width: 1200px;
    height: 800px;
    overflow: hidden;
    background: var(--backdrop);
    font-family: "Montserrat", sans-serif;
  }
  .canvas { position: relative; width: 1200px; height: 800px; }
  .card { position: absolute; left: 345px; width: 510px; height: 283px; }
  .card--front { top: 70px; }
  .card--back { top: 410px; }
  .card svg { display: block; width: 100%; height: 100%; }
  .name { font-weight: 500; font-size: 30px; fill: var(--text-light); }
  .role { font-weight: 400; font-size: 18px; fill: var(--text-light); }
  .contact { font-weight: 400; font-size: 17px; fill: var(--text-light); }
  .contact--email { font-size: 15.5px; }
  .web { font-weight: 400; font-size: 18px; }
  .web--dark { fill: var(--text-dark); }
  .web--light { fill: var(--text-light); }
  .company { font-weight: 500; fill: var(--text-dark); }
  .icon-disc { fill: var(--accent-yellow); }
  .icon-line { fill: none; stroke: var(--ink); stroke-width: 2; stroke-linejoin: round; }
</style>
</head>
<body>
<main class="canvas">

  <section class="card card--front" aria-label="Business card front">
    <svg viewBox="0 0 637 353" xmlns="http://www.w3.org/2000/svg">
      <defs>
        <clipPath id="front-shape"><rect width="637" height="353" rx="18"/></clipPath>
        <linearGradient id="front-paper" x1="0" y1="0" x2="1" y2="0">
          <stop offset="0" stop-color="var(--card-shade)"/>
          <stop offset="0.35" stop-color="var(--card-white)"/>
        </linearGradient>
      </defs>
      <g clip-path="url(#front-shape)">
        <rect class="paper" width="637" height="353" fill="url(#front-paper)"/>
        <path class="panel-dark" d="M93,0 H637 V292 Q450,262 255,284 Z" fill="var(--ink)"/>
        <path class="wave-stripe" d="M0,312 Q260,250 637,286 L637,294 Q290,266 0,324 Z" fill="var(--accent-yellow)"/>
        <path class="wave-base" d="M0,350 Q300,276 637,302 V353 H0 Z" fill="var(--accent-yellow)"/>
      </g>

      <text class="company" x="92" y="200" text-anchor="middle" font-size="17">Falkrin Homes</text>
      <text class="company" x="92" y="222" text-anchor="middle" font-size="17">and Renovations</text>

      <text class="name" x="298" y="43" text-anchor="middle">Dax Falkrin</text>
      <text class="role" x="298" y="70" text-anchor="middle">President and CEO</text>

      <text class="contact" x="565" y="106" text-anchor="end">403- 718-4063</text>
      <text class="contact" x="565" y="129" text-anchor="end">403- 294-5170</text>
      <text class="contact" x="565" y="160" text-anchor="end">2871 96th Avenue</text>
      <text class="contact" x="565" y="183" text-anchor="end">Frank, Alberta T2R3W8</text>
      <text class="contact contact--email" x="565" y="220" text-anchor="end">falkrinhomes@maildrop-example.net</text>

      <g class="icon icon--phone">
        <circle class="icon-disc" cx="595" cy="112" r="17"/>
        <rect class="icon-line" x="589" y="102" width="12" height="20" rx="2"/>
        <line class="icon-line" x1="593" y1="118" x2="597" y2="118"/>
      </g>
      <g class="icon icon--pin">
        <circle class="icon-disc" cx="595" cy="166" r="17"/>
        <path d="M595,178 C589,170 587,166 587,162 A8,8 0 0 1 603,162 C603,166 601,170 595,178 Z" fill="var(--ink)"/>
        <circle cx="595" cy="162" r="3" fill="var(--accent-yellow)"/>
      </g>
      <g class="icon icon--mail">
        <circle class="icon-disc" cx="595" cy="215" r="17"/>
        <rect class="icon-line" x="585" y="208" width="20" height="14"/>
        <polyline class="icon-line" points="585,208 595,216 605,208"/>
      </g>

      <text class="web web--dark" x="433" y="328" text-anchor="middle">www.falkrinhomes-example.com</text>
    </svg>
  </section>

  <section class="card card--back" aria-label="Business card back">
    <svg viewBox="0 0 637 353" xmlns="http://www.w3.org/2000/svg">
      <defs>
        <clipPath id="back-shape"><rect width="637" height="353" rx="18"/></clipPath>
      </defs>
      <g clip-path="url(#back-shape)">
        <rect class="paper" width="637" height="353" fill="var(--card-white)"/>
        <path class="wave-top" d="M0,0 H625 Q400,100 0,68 Z" fill="var(--accent-yellow)"/>
        <path class="wave-stripe" d="M0,82 Q340,118 637,38 V52 Q340,130 0,96 Z" fill="var(--accent-yellow)"/>
        <path class="wave-stripe" d="M0,318 Q300,262 637,294 V300 Q300,274 0,328 Z" fill="var(--accent-yellow)"/>
        <path class="wave-base" d="M0,353 Q220,290 637,305 V353 Z" fill="var(--ink)"/>
      </g>

      <text class="company" x="318" y="208" text-anchor="middle" font-size="30">Falkrin Homes and Renovations</text>

      <text class="web web--light" x="433" y="337" text-anchor="middle">www.falkrinhomes-example.com</text>
    </svg>
  </section>

</main>
</body>
</html>
```